Heron Loan Partners Business Card

We need a business card design for our mortgage servicing company. In addition to servicing the loans of homeowners, we help homeowners with purchasing their homes and any mortgage refinancing. We would like to see designs that use the colors in the logo attached below (gold-ish yellow and navy blue), and any other design you deem fit! The design should communicate a simpler life with smart mortgages provided by Heron.

```html
<!DOCTYPE html>
<html lang="en">
<head>
<meta charset="utf-8">
<title>Heron Loan Partners – Business Card</title>
<link rel="stylesheet" href="https://fonts.googleapis.com/css2?family=Playfair+Display:wght@700&family=Lora:wght@400;600&display=swap">
<style>
  :root {
    --gold: #dfb142;
    --navy: #25215a;
    --white: #ffffff;
    --ink: #1c1c28;
    --stage: #2e2e30;
    --rule: #1a1a1a;
  }
  * { margin: 0; padding: 0; box-sizing: border-box; }
  html, body { width: 1200px; height: 875px; overflow: hidden; }
  body {
    background: var(--stage);
    position: relative;
    font-family: "Lora", Georgia, serif;
  }
  .card {
    position: absolute;
    width: 520px;
    height: 300px;
    border-radius: 26px;
    overflow: hidden;
  }
  .card--front {
    left: 50px; top: 160px;
    background: var(--gold);
    display: flex; align-items: center; justify-content: center;
  }
  .card--back {
    left: 630px; top: 415px;
    background: var(--white);
    text-align: center;
    display: flex; flex-direction: column; align-items: center; justify-content: center;
  }
  .brand-name {
    font-family: "Playfair Display", Georgia, serif;
    font-weight: 700;
    color: var(--navy);
    line-height: 1;
  }
  .card--front .brand-name { font-size: 44px; }
  .card--back .brand-name { font-size: 30px; }
  .person-name {
    margin-top: 18px;
    font-size: 17px;
    font-weight: 600;
    letter-spacing: 0.06em;
    color: var(--navy);
  }
  .person-role {
    margin-top: 4px;
    font-size: 11px;
    letter-spacing: 0.08em;
    color: var(--navy);
  }
  .divider {
    margin-top: 14px;
    width: 440px;
    display: flex; align-items: center; gap: 10px;
  }
  .divider__line { flex: 1; height: 1px; background: var(--rule); }
  .divider__icons { display: flex; gap: 5px; }
  .icon { width: 20px; height: 20px; display: block; }
  .contact-list {
    list-style: none;
    margin-top: 12px;
    font-size: 12.5px;
    line-height: 1.55;
    color: var(--ink);
  }
</style>
</head>
<body>
  <section class="card card--front" aria-label="Card front">
    <p class="brand-name">Heron Loan Partners</p>
  </section>

  <section class="card card--back" aria-label="Card back">
    <p class="brand-name">Heron Loan Partners</p>
    <p class="person-name">DANIEL MERCER</p>
    <p class="person-role">MANAGING DIRECTOR</p>

    <div class="divider">
      <span class="divider__line"></span>
      <div class="divider__icons">
        <svg class="icon" viewBox="0 0 20 20" aria-label="Phone">
          <circle cx="10" cy="10" r="10" fill="var(--navy)"/>
          <path d="M6.5 5.5l2 0 1 2.5-1.2 1a6 6 0 0 0 2.7 2.7l1-1.2 2.5 1v2a1 1 0 0 1-1 1A8 8 0 0 1 5.5 6.5a1 1 0 0 1 1-1z" fill="var(--gold)"/>
        </svg>
        <svg class="icon" viewBox="0 0 20 20" aria-label="Email">
          <circle cx="10" cy="10" r="10" fill="var(--navy)"/>
          <rect x="5" y="6.5" width="10" height="7" fill="var(--gold)"/>
          <path d="M5 6.5l5 4 5-4" fill="none" stroke="var(--navy)" stroke-width="1"/>
        </svg>
        <svg class="icon" viewBox="0 0 20 20" aria-label="Website">
          <circle cx="10" cy="10" r="10" fill="var(--navy)"/>
          <g fill="none" stroke="var(--gold)" stroke-width="1.2">
            <circle cx="10" cy="10" r="5"/>
            <ellipse cx="10" cy="10" rx="2.2" ry="5"/>
            <path d="M5 10h10"/>
          </g>
        </svg>
        <svg class="icon" viewBox="0 0 20 20" aria-label="Location">
          <circle cx="10" cy="10" r="10" fill="var(--navy)"/>
          <path d="M10 4.5a4 4 0 0 1 4 4c0 3-4 7-4 7s-4-4-4-7a4 4 0 0 1 4-4z" fill="var(--gold)"/>
          <circle cx="10" cy="8.5" r="1.5" fill="var(--navy)"/>
        </svg>
      </div>
      <span class="divider__line"></span>
    </div>

    <ul class="contact-list">
      <li>071-580 392 614</li>
      <li>info@heronloan.com</li>
      <li>www.heronloanpartners.com</li>
      <li>88 Harbor Street, Suite 4, 30817 Westland</li>
    </ul>
  </section>
</body>
</html>
```